Stationery Design Project

I need a design that is simple, clean and modern, in square style, bold font.
The majority of the design needs to be White and Black with a splash of Red colour.
I would like a design for business cards and letter heads with the following information.
Name, Title, Phone, Fax, Email, Website and company ABN number

Target Market(s)

25 to 65 years old real estate clients

Industry/Entity Type

Business

Requirements
Must have
• All designs must incorporate Company Logo, Name, Title, Phone, Fax, Email, Website and company ABN number

```html
<!DOCTYPE html>
<html lang="en">
<head>
<meta charset="utf-8">
<title>Redcliff Real Estate – Business Card</title>
<link rel="stylesheet" href="https://fonts.googleapis.com/css2?family=PT+Sans:wght@400;700&display=swap">
<style>
  :root {
    --backdrop: #e8e4df;
    --card-white: #ffffff;
    --brand-red: #be1e2d;
    --ink: #231f20;
    --ink-soft: #3a3a3a;
  }
  * { box-sizing: border-box; margin: 0; padding: 0; }
  html, body { width: 1200px; height: 402px; overflow: hidden; }
  body {
    background: var(--backdrop);
    font-family: "PT Sans", Arial, sans-serif;
    position: relative;
  }
  .card {
    position: absolute;
    top: 54px;
    width: 512px;
    height: 292px;
    border-radius: 20px;
    overflow: hidden;
  }
  .card--front { left: 61px; background: var(--card-white); }
  .card--back { left: 639px; background: var(--brand-red); }

  .contact-band {
    position: absolute;
    left: 0; right: 0; bottom: 0;
    height: 86px;
    background: var(--brand-red);
  }

  .logo-frame {
    position: absolute;
    border-radius: 14px;
    display: flex;
    flex-direction: column;
    align-items: center;
    justify-content: center;
    font-weight: 700;
  }
  .card--front .logo-frame {
    left: 34px; top: 37px; width: 220px; height: 120px;
    border: 3px solid var(--ink);
    color: var(--ink);
  }
  .card--back .logo-frame {
    left: 104px; top: 44px; width: 306px; height: 168px;
    border: 4px solid var(--card-white);
    color: var(--card-white);
  }
  .logo-name { line-height: 1; letter-spacing: 1px; }
  .logo-sub { letter-spacing: 7px; margin-top: 10px; line-height: 1; }
  .card--front .logo-name { font-size: 40px; }
  .card--front .logo-sub { font-size: 11px; }
  .card--back .logo-name { font-size: 56px; }
  .card--back .logo-sub { font-size: 15px; letter-spacing: 10px; margin-top: 14px; }

  .person {
    position: absolute;
    right: 26px; top: 36px;
    text-align: right;
  }
  .person-name { color: var(--brand-red); font-weight: 700; font-size: 16px; line-height: 1.1; }
  .person-title { color: var(--ink-soft); font-size: 12px; line-height: 1.2; }

  .address {
    position: absolute;
    left: 34px; top: 170px;
    font-size: 12.5px;
    line-height: 15px;
    font-style: normal;
    color: var(--ink-soft);
  }

  .contact-list {
    position: absolute;
    right: 26px; bottom: 10px;
    list-style: none;
    color: var(--card-white);
    font-size: 12.5px;
    line-height: 16.5px;
    letter-spacing: 0.3px;
  }
  .contact-list li { display: flex; align-items: center; justify-content: flex-end; gap: 5px; }
  .contact-list svg { width: 10px; height: 10px; fill: var(--card-white); }

  .abn {
    position: absolute;
    left: 0; right: 0; top: 234px;
    text-align: center;
    color: var(--card-white);
    font-size: 16px;
  }
</style>
</head>
<body>

<section class="card card--front">
  <div class="contact-band"></div>

  <div class="logo-frame">
    <span class="logo-name">REDCLIFF</span>
    <span class="logo-sub">REAL ESTATE</span>
  </div>

  <div class="person">
    <p class="person-name">Your name</p>
    <p class="person-title">Title</p>
  </div>

  <address class="address">
    Street Name, City Name<br>
    State, City Zip Code
  </address>

  <ul class="contact-list">
    <li><svg viewBox="0 0 10 10" aria-hidden="true"><path d="M2,0.5 L3.6,2.8 L2.7,3.8 C3.3,5 4.8,6.6 6.2,7.3 L7.2,6.4 L9.5,8 L8.4,9.5 C4.5,9.2 0.8,5.5 0.5,1.6 Z"/></svg>123-456-7890</li>
    <li><svg viewBox="0 0 10 10" aria-hidden="true"><rect x="2.5" y="0.5" width="5" height="3"/><rect x="0.5" y="3.8" width="9" height="4" rx="1"/><rect x="2.5" y="7" width="5" height="2.5"/></svg>123-456-7890</li>
    <li><svg viewBox="0 0 10 10" aria-hidden="true"><path d="M0.5,2 H9.5 V8 H0.5 Z"/></svg>info@redcliffre.com</li>
    <li><svg viewBox="0 0 10 10" aria-hidden="true"><circle cx="5" cy="5" r="4.5"/></svg>www.redcliffre.com</li>
  </ul>
</section>

<section class="card card--back">
  <div class="logo-frame">
    <span class="logo-name">REDCLIFF</span>
    <span class="logo-sub">REAL ESTATE</span>
  </div>
  <p class="abn">ABN;123456789</p>
</section>

</body>
</html>
```